Equipment Finance Specialist I work with companies who need the funds to buy their equipment

I would like a business card that stands out on the shelves. I want to be able to hand it to someone and say WOW. This card should have my logo.
You can put color into it I am very open on design and color

What my company does is we deal with dealerships that sell equipment such as Dump Trucks garbage trucks tractors trailers. Customers get referred to us and depending on their time in business we will ask for the following items

Companies that have been in business for more than two years we have a credit application program up to 250K . With this program we need the following items Credit application filled out(which is what I would like to be able for the customer to click on my website to get.) as well as three current month bank statements.

Deals over 250k we will need the following items

2 years business tax returns
2 years personal tax returns
Profit & Loss statement
Personal Financial Statement

what we do
100% FINANCING
SEASONAL PAYMENTS
LOAN BALLOON PAYMENTS
TRAC LEASING
LOW-INTEREST REFINANCING RATES
DEBT CONSOLIDATION

We specialize in creative financing solutions and offer a variety of reliable, flexible and expandable lending choices.

Target Market(s)

Trucking Companies

Industry/Entity Type

Trucking Company

Contact Information for Business Card

* $250,000 Application only Program
* Loans from $30,000 to 5,000,000
* Competitive Interest Rates

Font styles to use
Serif
Sans Serif

Colors

Designer to choose colors to be used in the design.

Requirements
Must have
• On the back of the card.
• * $250,000 Application only Program
• * Loans from $30,000 to 5,000,000
• My name, email, website. address
• * Competitive Interest Rates
• * 100% Financing
Nice to have
• I want my logo to pop on the card
• My logo is the great one I would like to use
Should not have
• I am up for your creativity as well

```html
<!DOCTYPE html>
<html lang="en">
<head>
<meta charset="utf-8">
<title>Summit Lending – Business Card</title>
<link href="https://fonts.googleapis.com/css2?family=Open+Sans:wght@400;600;700;800&display=swap" rel="stylesheet">
<style>
  :root {
    --navy: #0b2a6b;
    --navy-deep: #08215a;
    --red: #d3142f;
    --ink: #2b2b2b;
    --white: #ffffff;
    --rule-light: rgba(255,255,255,0.28);
    --rule-dark: #c9ccd4;
    --backdrop: #e6e7ea;
  }
  * { box-sizing: border-box; margin: 0; padding: 0; }
  html, body { width: 1200px; height: 782px; overflow: hidden; }
  body {
    background: var(--backdrop);
    font-family: "Open Sans", Arial, sans-serif;
    display: flex;
    align-items: center;
    justify-content: center;
    gap: 40px;
  }
  .card {
    width: 540px;
    height: 309px;
    position: relative;
    overflow: hidden;
    box-shadow: 0 10px 28px rgba(0,0,0,0.18);
  }

  .brand {
    display: flex;
    align-items: center;
    gap: 10px;
    font-weight: 800;
    letter-spacing: 0.5px;
    text-transform: uppercase;
    white-space: nowrap;
  }
  .brand-dot { border-radius: 50%; flex: none; }

  /* Back side: navy */
  .card-back {
    background: var(--navy);
    color: var(--white);
    display: flex;
    flex-direction: column;
    align-items: center;
    justify-content: center;
    padding: 0 36px;
  }
  .card-back .brand { font-size: 32px; color: var(--white); }
  .card-back .brand-dot { background: var(--white); width: 40px; height: 40px; }
  .requirements {
    margin-top: 24px;
    text-align: center;
    font-size: 13.5px;
    line-height: 1.45;
  }
  .rule { width: 100%; height: 1px; background: var(--rule-light); }
  .rule-top { margin: 14px 0 10px; }
  .rule-bottom { margin-top: 10px; }
  .section-title { font-size: 12px; font-weight: 700; letter-spacing: 0.3px; }
  .services {
    list-style: none;
    display: flex;
    flex-wrap: wrap;
    justify-content: center;
    column-gap: 8px;
    row-gap: 3px;
    margin-top: 8px;
    font-size: 12px;
    text-transform: uppercase;
  }
  .services li::before { content: "\2022"; margin-right: 7px; }
  .services li.row-start::before,
  .services li.break::before { content: none; }
  .services .break { flex-basis: 100%; height: 0; }

  /* Front side: white */
  .card-front {
    background: var(--white);
    color: var(--ink);
    display: flex;
    padding: 44px 28px 0 30px;
  }
  .card-front::after {
    content: "";
    position: absolute; left: 0; right: 0; bottom: 0;
    height: 16px;
    background: var(--navy);
  }
  .front-left { width: 236px; flex: none; }
  .card-front .brand { font-size: 20px; color: var(--navy); gap: 8px; }
  .card-front .brand-dot { background: var(--red); width: 24px; height: 24px; }
  .divider {
    width: 1px;
    height: 196px;
    background: var(--rule-dark);
    margin: 6px 18px 0 6px;
    flex: none;
  }
  .highlights { list-style: none; font-size: 13px; line-height: 1.4; }
  .highlights li { position: relative; padding-left: 12px; white-space: nowrap; }
  .highlights li::before {
    content: "";
    position: absolute; left: 0; top: 7px;
    width: 6px; height: 6px; border-radius: 50%;
    background: var(--red);
  }
  .front-left .highlights { margin-top: 62px; }
  .front-right { flex: 1; }
  .person-name {
    font-size: 19px;
    font-weight: 700;
    color: var(--navy);
    letter-spacing: 0.4px;
    text-transform: uppercase;
    line-height: 1.1;
  }
  .person-title { font-size: 13px; color: var(--red); margin-bottom: 6px; }
  .contacts { list-style: none; font-size: 13px; line-height: 1.45; }
  .contacts li { display: flex; align-items: center; gap: 7px; }
  .contacts svg { width: 12px; height: 12px; fill: var(--navy-deep); flex: none; }
  .address { font-size: 13px; line-height: 1.35; margin-top: 2px; }
  .front-right .highlights { margin-top: 14px; }
</style>
</head>
<body>

  <section class="card card-back" aria-label="Card back">
    <div class="brand"><span class="brand-dot"></span>Summit Lending</div>
    <p class="requirements">
      2 years business tax returns | 2 years personal tax returns<br>
      Profit &amp; Loss statement | Personal Financial Statement
    </p>
    <div class="rule rule-top"></div>
    <h2 class="section-title">WHAT WE DO</h2>
    <ul class="services">
      <li class="row-start">100% Financing</li>
      <li>Seasonal Payments</li>
      <li>Loan Balloon Payments</li>
      <li class="break" aria-hidden="true"></li>
      <li class="row-start">TRAC Leasing</li>
      <li>Low-Interest Refinancing Rates</li>
      <li>Debt Consolidation</li>
    </ul>
    <div class="rule rule-bottom"></div>
  </section>

  <section class="card card-front" aria-label="Card front">
    <div class="front-left">
      <div class="brand"><span class="brand-dot"></span>Summit Lending</div>
      <ul class="highlights">
        <li>$250,000 Application only Program</li>
        <li>Loans from $30,000 to 5,000,000</li>
      </ul>
    </div>
    <div class="divider"></div>
    <div class="front-right">
      <h1 class="person-name">Daniel Harper</h1>
      <p class="person-title">Managing Director</p>
      <ul class="contacts">
        <li><svg viewBox="0 0 24 24" aria-hidden="true"><path d="M6.6 10.8a15 15 0 0 0 6.6 6.6l2.2-2.2a1 1 0 0 1 1-.25 11.4 11.4 0 0 0 3.6.57 1 1 0 0 1 1 1V20a1 1 0 0 1-1 1A17 17 0 0 1 3 4a1 1 0 0 1 1-1h3.5a1 1 0 0 1 1 1c0 1.25.2 2.45.57 3.57a1 1 0 0 1-.25 1z"/></svg>044-987 654 321</li>
        <li><svg viewBox="0 0 24 24" aria-hidden="true"><path d="M2 5h20v14H2zm2 2v.5l8 5 8-5V7zm0 2.8V17h16V9.8l-8 5z"/></svg>info@summitlending.com</li>
        <li><svg viewBox="0 0 24 24" aria-hidden="true"><circle cx="12" cy="12" r="10"/></svg>www.summitlending.com</li>
      </ul>
      <p class="address">76 Harbor Road, Suite 12,<br>60318, Lakeshire</p>
      <ul class="highlights">
        <li>Competitive Interest Rates</li>
        <li>100% Financing</li>
      </ul>
    </div>
  </section>

</body>
</html>
```